Innovative WordPress for a non-profit organization dedicated to providing healthcare to the less for

Bright Harbor Aid is a small non-profit organization. BHA's core mission is to provide free medical and dental care to the less fortunate. Aside from providing healthcare, BHA also helps build infrastructure such as orphanage, cancer centers, water wells and small homes for the homeless. As a non-profit, BHA has been sponsoring various social programs to help those in need. From building infrastructure to health care and most recently micro-finance, the BHA team is helping to GIve Back to the community at person at a time.

BHA is growing and needs help to restructure for the future. The corporate website design is the first step in a new branding strategy for the company.

BHA current website is divided into three specific target areas:
1. Mission: This area is dedicated to provide information about medical and dental mission hosted by BHA.

2. Infrastructure. This area is dedicated to provide information about infrastructure programs supported and completed by the BHA team. The projects includes orphanage, cancer centers. water wells, micro-finance, small homes for the homeless...etc.

3. Special Projects. This area is used to showcase specific short term projects which might come up.

Aside from the specific three target area, BHA also needs a NEWS area where news about BHA can be published.

Please put your thinking cape on and help produce the next generation WordPress template for Bright Harbor Aid. Your design will great enhance the level of volunteers recruited and also increase the level of help that BHA can provide for other.

For a quick glance at the BHA website today, please visit http://www.brightharboraid-example.org. The BHA team is looking for a fresh design.

Thank you very much for taking the time to help BHA advance its mission of helping those in need.

Reason: Seeking more variety in design. Design needs to have a donate button, sponsors area, news, welcome message, 3 primary functions (mission, infrastructure, and specials projects). The BHA logo is available. Please note, you have the option to NOT use the colors associated with BHA logo. Thank you for helping with designing the new site.

Non-Profit

Requirements
Must have
• 1. Donate Now button.
2. Primary focus areas: MISSION / INFRASTRUCTURE / SPECIAL PROJECTS
3. News & Events
4. Welcome Message area
5. Sponsors area - place to add sponsor logos

Nice to have
• 1. Photo of the Month: Used to show a specific photo to represent events or functions completed by the BHA team.

Please show sample of one level down. For example, what does the page look like when I click the MISSION link.

```html
<!DOCTYPE html>
<html lang="en">
<head>
<meta charset="utf-8">
<title>Bright Harbor Aid — Home</title>
<link href="https://fonts.googleapis.com/css2?family=Arimo:wght@400;700&display=swap" rel="stylesheet">
<style>
:root{
  --green:#1f9b3c;
  --green-dark:#16762c;
  --green-light:#39b54a;
  --red:#e31e24;
  --ink:#222;
  --muted:#444;
  --grey-bg:#efefef;
  --black:#111;
  --white:#fff;
}
*{box-sizing:border-box;margin:0;padding:0}
html,body{width:933px;height:1200px;overflow:hidden}
body{position:relative;font-family:"Arimo",Arial,sans-serif;color:var(--ink);background:var(--grey-bg)}
.abs{position:absolute}

.site-header{left:0;top:0;width:933px;height:88px;background:var(--white)}
.top-band{left:0;top:88px;width:933px;height:340px;background:linear-gradient(#7a7a7a,#5e5e5e 60%,#6a6a6a)}
.tagline{left:455px;top:16px;font-size:21px;color:#444}
.search-field{left:573px;top:49px;width:150px;height:19px;border:1px solid #bbb;background:var(--white)}
.search-btn{left:730px;top:49px;width:67px;height:19px;background:var(--red);color:var(--white);font-size:11px;text-align:center;line-height:19px;border-radius:2px}
.donate-btn{left:810px;top:46px;width:100px;height:25px;background:linear-gradient(var(--green-light),var(--green-dark));color:var(--white);font-size:12px;font-weight:700;text-align:center;line-height:25px;border-radius:3px}

.logo-tab{left:141px;top:25px;width:202px;height:88px;background:linear-gradient(#fff,#ececec);border-radius:6px 6px 0 0;box-shadow:0 -1px 4px rgba(0,0,0,.25);display:flex;align-items:center;justify-content:center;gap:8px}
.logo-dot{width:18px;height:18px;border-radius:50%;background:var(--green)}
.logo-name{font-size:34px;font-weight:700;color:var(--green-dark)}

.main-nav{left:126px;top:110px;width:681px;height:31px;background:linear-gradient(var(--green-light),var(--green-dark));display:flex;border-radius:3px 3px 0 0}
.main-nav span{flex:1;color:var(--white);font-size:13px;text-align:center;line-height:31px;border-right:1px solid rgba(255,255,255,.35)}
.main-nav span:last-child{border-right:0}

.hero{left:126px;top:141px;width:681px;height:299px;background:linear-gradient(100deg,#5c6a3e,#c9b7a6 35%,#d8d0c6 55%,#8a7a66 80%,#3e4a2e)}
.hero-caption{left:126px;top:346px;width:681px;height:63px;background:rgba(60,60,60,.55);text-align:center;color:var(--white)}
.hero-caption h2{font-size:19px;font-weight:700;line-height:20px;margin-top:4px}
.hero-caption p{font-size:12px;margin-top:4px}
.hero-arrow{top:282px;width:20px;height:40px;background:rgba(40,40,40,.75);color:var(--white);font-size:22px;line-height:40px;text-align:center}
.slider-base{left:126px;top:432px;width:681px;height:34px;background:linear-gradient(#fff,#e2e2e2);border-radius:0 0 8px 8px;box-shadow:0 2px 4px rgba(0,0,0,.2)}
.slider-dots{left:421px;top:434px;width:100px;height:28px;background:var(--white);border-radius:4px;box-shadow:0 1px 3px rgba(0,0,0,.3);display:flex;align-items:center;justify-content:center;gap:4px}
.slider-dots i{width:13px;height:13px;border-radius:50%;background:#aaa}
.slider-dots i.on{background:var(--red)}

.news-ticker{left:126px;top:472px;width:681px;height:19px;display:flex;align-items:center;font-size:10.5px;color:#333}
.news-label{background:var(--green);color:var(--white);font-weight:700;padding:0 8px;line-height:19px;margin-right:10px;border-radius:2px}
.news-ticker .sep{color:#999;margin:0 8px}

.content-panel{left:126px;top:497px;width:681px;height:560px;background:var(--white);border-radius:8px;box-shadow:0 0 4px rgba(0,0,0,.2)}
.welcome{left:126px;top:510px;width:681px;text-align:center;font-size:33px;font-weight:400;color:#333}
.welcome em{font-style:normal;color:var(--green)}
.body-text{font-size:9.6px;line-height:11.8px;color:var(--muted);text-align:justify}
.intro{left:141px;top:579px;width:412px}
.history{left:141px;top:701px;width:649px}
.history p+p{margin-top:11px}

.newsletter{left:570px;top:574px;width:220px;height:113px;background:linear-gradient(var(--green),var(--green-dark));color:var(--white)}
.newsletter-head{height:24px;background:var(--green-dark);font-size:16px;line-height:24px;padding-left:10px;color:#f3e14b}
.newsletter-badge{left:186px;top:6px;width:20px;height:20px;background:var(--red);transform:rotate(12deg)}
.newsletter p{font-size:11.5px;line-height:13px;padding:18px 0 0 20px}
.nl-field{left:20px;top:76px;width:135px;height:16px;background:var(--white);color:#333;font-size:8px;line-height:16px;padding-left:6px}
.nl-btn{left:159px;top:76px;width:49px;height:16px;background:var(--red);font-size:9px;line-height:16px;text-align:center;font-weight:700}

.focus-card{top:858px;width:210px;height:184px;background:var(--white);box-shadow:0 1px 5px rgba(0,0,0,.35);padding:6px 12px 0}
.focus-card h3{font-size:16px;font-weight:400;text-align:center;color:#333;letter-spacing:.5px}
.focus-photo{width:186px;height:71px;margin-top:4px}
.focus-card p{font-size:9px;line-height:10.5px;color:#333;margin-top:4px}
.read-more{display:block;width:64px;height:15px;margin:6px auto 0;background:var(--red);color:var(--white);font-size:8.5px;line-height:15px;text-align:center;border-radius:2px}

.site-footer{left:0;top:1045px;width:933px;height:155px;background:linear-gradient(#2b2b2b,var(--black))}
.footer-bar{left:126px;top:1068px;width:681px;height:46px;background:#1a1a1a;border-radius:0 0 10px 10px}
.footer-nav{left:126px;top:1093px;width:681px;display:flex;justify-content:space-around;color:var(--white);font-size:12px}
.sponsors{left:140px;top:1122px;color:var(--white);font-size:9px}
.sponsor-row{left:140px;top:1136px;display:flex;gap:8px}
.sponsor-row i{width:52px;height:20px;background:#4a4a4a;border-radius:2px}
.footer-logo{left:403px;top:1120px;display:flex;align-items:center;gap:5px}
.footer-logo span{font-size:20px;font-weight:700;color:var(--green-light)}
.footer-logo i{width:10px;height:10px;border-radius:50%;background:var(--green-light)}
.follow{left:507px;top:1122px;color:var(--white);font-size:9px}
.social{left:489px;top:1136px;display:flex;gap:5px}
.social i{width:18px;height:18px;border-radius:3px;background:#3b6cb5}
.copyright-pill{left:289px;top:1170px;width:360px;height:30px;background:#000;border-radius:14px 14px 0 0;color:var(--white);font-size:11px;text-align:center;line-height:32px}
</style>
</head>
<body>
<header class="abs site-header"></header>
<div class="abs top-band"></div>
<div class="abs tagline">Serving The Disadvantage Community</div>
<div class="abs search-field"></div>
<div class="abs search-btn">Search</div>
<div class="abs donate-btn">Donate Now</div>
<div class="abs logo-tab"><i class="logo-dot"></i><span class="logo-name">BHA</span></div>

<nav class="abs main-nav"><span>Home</span><span>About Us</span><span>Mission</span><span>Special Projects</span><span>Infrastructure</span><span>Events</span></nav>

<div class="abs hero" role="img" aria-label="Photo of smiling volunteers in white uniforms at a dental clinic"></div>
<div class="abs hero-caption">
  <h2>Dr. Mara Ellison (far right) working with the volunteers<br>at a BHA dental clinic</h2>
  <p>Dr. Mara Ellison mentoring group of volunteers who will be future dentist at the BHA Dental</p>
</div>
<div class="abs hero-arrow" style="left:126px">&#8249;</div>
<div class="abs hero-arrow" style="left:787px">&#8250;</div>
<div class="abs slider-base"></div>
<div class="abs slider-dots"><i class="on"></i><i></i><i></i><i></i><i></i></div>

<div class="abs news-ticker"><span class="news-label">News &amp; Events</span><span>Free dental clinic this spring — volunteers wanted</span><span class="sep">|</span><span>New water well project completed</span></div>

<main class="abs content-panel"></main>
<h1 class="abs welcome">Welcome To <em>BrightHarborAid.org</em></h1>
<div class="abs body-text intro">Bright Harbor Aid (BHA) is non profit - 501 C (3) organization dedicated to providing health-care. Human services, and educational assistance to underprivilleged communities. we work in collaboration with various groups and non-governmental organizations (NGOs). to delivere humanitarian goods, services and relief to improverished regions. The team is comprised of professionals with a broadspectrum of experiences. the combined mission trips of our team span across north America, South Africa, South America, and South East Asia, bringing a variety of general and specialized disciplines to each region.</div>

<aside class="abs newsletter">
  <div class="newsletter-head">Newsletter</div>
  <div class="abs newsletter-badge"></div>
  <p>Sign Up and start receive<br>our newsletter weekly</p>
  <div class="abs nl-field">Your email address</div>
  <div class="abs nl-btn">SUBMIT</div>
</aside>

<div class="abs body-text history">
  <p>The BHA team initial medical mission project was Phnom Penh, Cambodia in March 2005. The mission team provided care to over 2.500 patients. in november 2005, The BHA Team collaborated with Coastal Relief for the Disabled (CRD) to bring a medical, Dental and public Health mission to Da Nang. Vietnam. This medical mission provided treatments to over 2.700 students from first to fifth grades. The team served students five elementary schools, delivering over 1.500 dental procedurs and 500 medical examinations. The team also successfully introduced public health program including basic and oral higienic training for all students and their parents. Such training is intended to help reduce the risk of disease and infection over time.</p>
  <p>From the experiences of the first two mission trips, Bright Harbor Aid (BHA) was formally incorporated in August 2006. As a formally incorporated and qualified non-profit organization, BHA is better positioned to provide assistance to those in need. From 2006 to present, The BHA team has grown and diversified exponentially. BHA's primary mission is focused toward providing health care services to the disadvanrage community. Building infrastucture such as orphanage, cancer centers and other special programs.</p>
</div>

<section class="abs focus-card" style="left:147px">
  <h3>MISSION</h3>
  <div class="focus-photo" role="img" aria-label="Photo of a mission team gathered beside a clinic sign" style="background:linear-gradient(90deg,#b58a6a,#d9cfc2 55%,#8d9a6d)"></div>
  <p>Through the years. Bright Harbor Aid has hosted numerous different type of dental/ medical missions. Most recently, the BHA team hosted a free dental clinic at the ...</p>
  <span class="read-more">Read more</span>
</section>
<section class="abs focus-card" style="left:364px">
  <h3>INFRASTRUCTURE</h3>
  <div class="focus-photo" role="img" aria-label="Photo of a cancer center building with a tiled roof" style="background:linear-gradient(180deg,#c9d3dc,#b6826a 55%,#7d6a58)"></div>
  <p>Linden Cancer Center - and House Aside from hosting various dental and medical missions through out the year. the BHA team also engages in infrastructure ...</p>
  <span class="read-more">Read more</span>
</section>
<section class="abs focus-card" style="left:576px">
  <h3>SPECIAL PROJECTS</h3>
  <div class="focus-photo" role="img" aria-label="Photo of a volunteer group in green shirts outdoors" style="background:linear-gradient(180deg,#8fa0b0,#a6c95a 50%,#5b7a3a)"></div>
  <p>Through the years. Bright Harbor Aid has hosted numerous different type of dental/ medical missions. Most recently, the BHA team hosted a free dental clinic at the ...</p>
  <span class="read-more">Read more</span>
</section>

<footer class="abs site-footer"></footer>
<div class="abs footer-bar"></div>
<nav class="abs footer-nav"><span>Home</span><span>About Us</span><span>Mission</span><span>Special Projects</span><span>Infrastructure</span><span>Events</span></nav>
<div class="abs sponsors">OUR SPONSORS :</div>
<div class="abs sponsor-row" role="img" aria-label="Sponsor logo placeholders"><i></i><i></i><i></i><i></i></div>
<div class="abs footer-logo"><i></i><span>BHA</span></div>
<div class="abs follow">FOLLOW US ON :</div>
<div class="abs social"><i></i><i style="background:#c4302b"></i><i style="background:#0e76a8"></i><i style="background:#3aa0d8"></i><i style="background:#2b9a4a"></i></div>
<div class="abs copyright-pill">Copyright &copy; 2014, BrightHarborAid.org. All rights reserved.</div>
</body>
</html>
```